Business card design Needed for new logo / Construction business, home extensions and new builds

We need a business card design using our new logo files which i will attach to this project :)

We are a small construction business specialising in home extensions, new builds and property development. We are very ambitious and would appreciate professional and elegant designs for our new business card.

Very serious about using the services on MakerQuarry and recently acquired our new logo from here :)

Please get involved, i will feedback when i can as i am very busy but can respond daily, thanks

Target Market(s)

People that want to build onto their houses, new building developments or adding too their existing property

Industry/Entity Type

Construction

Contact Information for Business Card

Renwick Tolliver Construction, Lionel Ashby (Managing Director), Tel 07822254961, email - info@renwick-tolliver, www.renwick-tolliver.co.uk

Colors

Designer to choose colors to be used in the design.

Requirements
Must have
• I like a deep grey on the back please. A lot of you have provided black from and back, try mixing things up a little. The black looks cool 😎 Thanks

```html
<!DOCTYPE html>
<html lang="en">
<head>
<meta charset="utf-8">
<title>Renwick Tolliver Construction – Business Card</title>
<link rel="stylesheet" href="https://fonts.googleapis.com/css2?family=Open+Sans:wght@400;600;700&display=swap">
<style>
  :root {
    --page: #34343a;
    --card-back: #202024;
    --card-front: #1d1d21;
    --emboss: #303036;
    --gold: #d9a537;
    --gold-light: #f3cf6a;
    --gold-deep: #b07e1f;
    --silver: #d4d6da;
    --white: #f4f4f4;
  }
  * { margin: 0; padding: 0; box-sizing: border-box; }
  html, body { width: 1200px; height: 780px; overflow: hidden; }
  body {
    background: var(--page);
    font-family: "Open Sans", Arial, sans-serif;
    position: relative;
  }
  .card {
    position: absolute;
    top: 233px;
    width: 550px;
    height: 314px;
    border-radius: 4px;
    overflow: hidden;
  }
  .card--back { left: 30px; background: var(--card-back); }
  .card--front { left: 620px; background: var(--card-front); }

  /* Back */
  .back-brand {
    position: absolute;
    inset: 0;
    display: flex;
    flex-direction: column;
    align-items: center;
    justify-content: center;
    gap: 14px;
    color: var(--emboss);
    font-weight: 700;
    text-transform: uppercase;
    text-align: center;
  }
  .back-brand__mark { width: 46px; height: 46px; background: var(--emboss); }
  .back-brand__name { font-size: 26px; letter-spacing: 3px; line-height: 1.25; }

  /* Front brand */
  .front-brand {
    position: absolute;
    left: 190px;
    top: 46px;
    display: flex;
    align-items: center;
    gap: 12px;
  }
  .front-brand__mark { width: 26px; height: 26px; background: var(--gold); flex: none; }
  .front-brand__name {
    color: var(--silver);
    font-weight: 600;
    font-size: 16px;
    letter-spacing: 2px;
    line-height: 1.3;
    text-transform: uppercase;
  }

  /* Person */
  .person { position: absolute; left: 34px; top: 168px; }
  .person__name { font-size: 28px; font-weight: 700; line-height: 1; }
  .person__first { color: var(--silver); }
  .person__last { color: var(--gold); }
  .person__role { color: var(--white); font-size: 14px; margin-top: 6px; padding-left: 70px; }

  .divider {
    position: absolute;
    left: 300px;
    top: 138px;
    width: 1px;
    height: 92px;
    background: linear-gradient(var(--card-front), var(--silver) 50%, var(--card-front));
    transform: rotate(-18deg);
  }

  /* Contacts */
  .contacts {
    position: absolute;
    left: 332px;
    top: 142px;
    list-style: none;
    color: var(--white);
    font-size: 12.5px;
    line-height: 1;
  }
  .contacts li { display: flex; align-items: center; gap: 8px; margin-bottom: 10px; }
  .contacts svg { width: 12px; height: 12px; flex: none; }

  /* Address band */
  .address-band {
    position: absolute;
    left: 0;
    right: 0;
    top: 262px;
    height: 22px;
    background: linear-gradient(180deg, var(--gold-light), var(--gold) 45%, var(--gold-deep));
    color: var(--white);
    font-size: 12px;
    font-weight: 600;
    line-height: 22px;
    text-align: center;
    letter-spacing: 0.3px;
  }
</style>
</head>
<body>

<section class="card card--back" aria-label="Card back">
  <div class="back-brand">
    <span class="back-brand__mark"></span>
    <p class="back-brand__name">Renwick Tolliver<br>Construction</p>
  </div>
</section>

<section class="card card--front" aria-label="Card front">
  <div class="front-brand">
    <span class="front-brand__mark"></span>
    <p class="front-brand__name">Renwick Tolliver<br>Construction</p>
  </div>

  <div class="person">
    <p class="person__name"><span class="person__first">Lionel</span> <span class="person__last">Ashby</span></p>
    <p class="person__role">Managing Director</p>
  </div>

  <span class="divider"></span>

  <ul class="contacts">
    <li>
      <svg viewBox="0 0 24 24" aria-hidden="true"><path fill="var(--gold)" d="M6.6 10.8a15.1 15.1 0 0 0 6.6 6.6l2.2-2.2a1 1 0 0 1 1-.25 11.4 11.4 0 0 0 3.6.57 1 1 0 0 1 1 1V20a1 1 0 0 1-1 1A17 17 0 0 1 3 4a1 1 0 0 1 1-1h3.5a1 1 0 0 1 1 1c0 1.25.2 2.45.57 3.57a1 1 0 0 1-.25 1z"/></svg>
      0782 225 4961
    </li>
    <li>
      <svg viewBox="0 0 24 24" aria-hidden="true"><rect x="2" y="5" width="20" height="14" rx="2" fill="var(--gold)"/><path d="M3 6l9 7 9-7" fill="none" stroke="var(--card-front)" stroke-width="2"/></svg>
      info@renwick-tolliver.co.uk
    </li>
    <li>
      <svg viewBox="0 0 24 24" aria-hidden="true"><circle cx="12" cy="12" r="10" fill="var(--gold)"/><path d="M2 12h20M12 2c3 3 3 17 0 20M12 2c-3 3-3 17 0 20" fill="none" stroke="var(--card-front)" stroke-width="1.5"/></svg>
      www.renwick-tolliver.co.uk
    </li>
  </ul>

  <p class="address-band">Harrow Lane, Eastfield Dunmore, DN4 7QT</p>
</section>

</body>
</html>
```